Web Developer Needs a Business Card Design

I need a personal business card design that represents me as a web developer for potential employers. I would like the background to be a dark color on the front for contrast with my logo and name. The back will have all my information along with a smaller version of the logo. I want something with a modern look and feel, not too conservative. This will be used for potential employers and freelance work.

Industry/Entity Type

Business

Contact Information for Business Card

Front should have my logo and name. The back should have all my personal information which would include: name: Tom Varulek, phone: 570-614-3098, email: tomvarulek@quillbox.net, website url: www.tomvarulek.net, logo, web developer.

Font styles to use
Sans Serif

Requirements
Must have
• Must include my logo. The color palette base color will be the logo color.

```html
<!DOCTYPE html>
<html lang="en">
<head>
<meta charset="utf-8">
<title>Tom Varulek — Business Card</title>
<link rel="stylesheet" href="https://fonts.googleapis.com/css2?family=Federo&family=Arimo:ital@0;1&display=swap">
<style>
  :root {
    --mint: #5ae6c8;
    --carbon-dark: #0b0b0c;
    --carbon-mid: #232325;
    --carbon-light: #2e2e30;
  }
  html, body {
    margin: 0;
    padding: 0;
    width: 1200px;
    height: 683px;
    overflow: hidden;
    background: var(--carbon-dark);
  }
  .card {
    position: relative;
    width: 1200px;
    height: 683px;
    overflow: hidden;
    background: linear-gradient(160deg, var(--carbon-light) 0%, var(--carbon-mid) 35%, #151517 70%, var(--carbon-dark) 100%);
  }
  .texture {
    position: absolute;
    inset: 0;
  }
  .emblem {
    position: absolute;
    left: 0;
    top: 0;
    width: 620px;
    height: 600px;
  }
  .emblem-ring {
    fill: none;
    stroke: var(--mint);
    stroke-width: 20;
  }
  .emblem-name {
    font-family: "Federo", sans-serif;
    font-size: 96px;
    fill: var(--mint);
  }
  .identity {
    position: absolute;
    left: 639px;
    top: 310px;
    width: 515px;
  }
  .identity-name {
    margin: 0;
    font-family: "Federo", sans-serif;
    font-weight: 400;
    font-size: 74px;
    line-height: 1;
    color: var(--mint);
    text-align: center;
    white-space: nowrap;
    padding-bottom: 6px;
    border-bottom: 4px solid var(--mint);
  }
  .identity-role {
    margin: 10px -12px 0 0;
    font-family: "Arimo", sans-serif;
    font-style: italic;
    font-size: 31px;
    color: var(--mint);
    text-align: right;
  }
  .contact {
    position: absolute;
    left: 530px;
    top: 522px;
    width: 641px;
    font-family: "Arimo", sans-serif;
    font-size: 32px;
    color: var(--mint);
  }
  .contact-row {
    display: flex;
    height: 42.5px;
    align-items: baseline;
  }
  .contact-label { width: 195px; }
  .contact-sep { width: 30px; }
  .contact-value { flex: 1; text-align: right; white-space: nowrap; }
</style>
</head>
<body>
  <main class="card">
    <div class="texture" role="img" aria-label="Dark carbon-fibre weave background"></div>

    <svg class="emblem" viewBox="0 0 620 600" aria-label="Tom Varulek emblem">
      <circle class="emblem-ring" cx="279" cy="257" r="322"/>
      <text class="emblem-name" x="279" y="300" text-anchor="middle">varulek</text>
    </svg>

    <header class="identity">
      <h1 class="identity-name">Tom Varulek</h1>
      <p class="identity-role">logo and web developer</p>
    </header>

    <section class="contact">
      <div class="contact-row"><span class="contact-label">phone</span><span class="contact-sep">:</span><span class="contact-value">570-614-3098</span></div>
      <div class="contact-row"><span class="contact-label">&nbsp;email</span><span class="contact-sep">:</span><span class="contact-value">tomvarulek@quillbox.net</span></div>
      <div class="contact-row"><span class="contact-label">website</span><span class="contact-sep">:</span><span class="contact-value">www.tomvarulek.net</span></div>
    </section>
  </main>
</body>
</html>
```